Business card for Luxury Portable Restroom Trailer company

We are a Luxury Portable Restroom Trailer Company Called FALCRIDGE HIRES. Based in Orange County California. We provide portable restroom trailers for events, such as, Weddings, Concerts, Charity events, Sporting events, Tournaments, Corporate events, ect. We rent and Sell the Luxury restrooms. Our colors are white, grey, and Orange. As you will see in the logo we uploaded.
There are 2 people in the company so the names and titles will change for the 3 people but card will remain the same. Here is the information for each Person: Dwight Penner CFO 555 318-0476
next Person: Leon Marchetti VP 555 318-0476
Next Person: Owen Marchetti CEO 555 318-0476
Information to include on the card: Luxury Restroom Trailers Rental and Sales. Weddings, Concerts, Charity, Sporting and Corp. Events.

```html
<!DOCTYPE html>
<html lang="en">
<head>
<meta charset="utf-8">
<title>Falcridge Hires – Business Card</title>
<link href="https://fonts.googleapis.com/css2?family=Roboto:wght@400;500;900&display=swap" rel="stylesheet">
<style>
  :root {
    --backdrop: #3b3b3d;
    --card: #2f2f31;
    --card-edge: #262628;
    --orange: #f26a1b;
    --white: #f4f4f4;
    --grey: #8c8c8e;
    --relief: #3a3a3c;
  }
  html, body {
    margin: 0;
    width: 1200px;
    height: 689px;
    overflow: hidden;
    background: var(--backdrop);
    font-family: "Roboto", Arial, sans-serif;
  }
  .stage {
    position: relative;
    width: 1200px;
    height: 689px;
  }
  .card {
    position: absolute;
    top: 196px;
    width: 520px;
    height: 297px;
    background: var(--card);
    border-radius: 14px;
    box-sizing: border-box;
    border-bottom: 3px solid var(--orange);
    box-shadow: 0 8px 24px rgba(0,0,0,0.35);
  }
  .card--back { left: 50px; }
  .card--front { left: 630px; }

  /* back side */
  .card--back .wordmark {
    position: absolute;
    left: 50%;
    top: 92px;
    transform: translateX(-50%);
    display: flex;
    align-items: center;
    gap: 12px;
    padding: 12px 20px;
    border: 2px solid var(--grey);
    white-space: nowrap;
  }
  .wordmark__square {
    width: 22px;
    height: 22px;
    background: var(--grey);
  }
  .wordmark__name {
    font-weight: 900;
    font-size: 30px;
    letter-spacing: 1px;
    color: var(--grey);
  }
  .tagline {
    position: absolute;
    left: 0;
    right: 0;
    top: 196px;
    text-align: center;
    color: var(--white);
    font-size: 14px;
    line-height: 20px;
    margin: 0;
  }

  /* front side */
  .card--front .frame {
    position: absolute;
    inset: 10px;
    border: 1.5px solid var(--orange);
    border-radius: 9px;
  }
  .card--front .wordmark {
    position: absolute;
    left: 34px;
    top: 40px;
    display: flex;
    align-items: center;
    gap: 8px;
    padding: 6px 10px;
    border: 2px solid var(--orange);
  }
  .card--front .wordmark__square {
    width: 13px;
    height: 13px;
    background: var(--orange);
  }
  .card--front .wordmark__name {
    font-size: 17px;
    color: var(--orange);
    letter-spacing: 0.5px;
  }
  .emblem {
    position: absolute;
    right: 34px;
    top: 38px;
    width: 200px;
    height: 200px;
  }
  .person {
    position: absolute;
    left: 34px;
    top: 150px;
  }
  .person__name {
    margin: 0;
    font-size: 19px;
    font-weight: 500;
    color: var(--orange);
    text-transform: uppercase;
  }
  .person__title {
    margin: 2px 0 0;
    font-size: 12px;
    color: var(--white);
  }
  .contact {
    list-style: none;
    position: absolute;
    left: 34px;
    top: 212px;
    margin: 0;
    padding: 0;
    color: var(--white);
    font-size: 12.5px;
  }
  .contact li {
    display: flex;
    align-items: center;
    gap: 8px;
    height: 18px;
  }
  .contact svg { width: 11px; height: 11px; fill: var(--orange); }
</style>
</head>
<body>
<main class="stage">

  <section class="card card--back" aria-label="Card back">
    <div class="wordmark">
      <span class="wordmark__square"></span>
      <span class="wordmark__name">FALCRIDGE HIRES</span>
    </div>
    <p class="tagline">Luxury Restroom Trailers Rental and Sales.<br>
      Weddings • Concerts • Charity • Sporting and Corp. Events</p>
  </section>

  <section class="card card--front" aria-label="Card front">
    <div class="frame"></div>
    <div class="wordmark">
      <span class="wordmark__square"></span>
      <span class="wordmark__name">FALCRIDGE HIRES</span>
    </div>

    <svg class="emblem" viewBox="0 0 200 200" aria-hidden="true">
      <circle cx="100" cy="100" r="96" fill="none" stroke="var(--relief)" stroke-width="6"/>
      <circle cx="100" cy="100" r="86" fill="var(--relief)" opacity="0.35"/>
    </svg>

    <div class="person">
      <h1 class="person__name">Dwight Penner</h1>
      <p class="person__title">CFO</p>
    </div>

    <ul class="contact">
      <li>
        <svg viewBox="0 0 24 24"><path d="M6.6 10.8c1.4 2.8 3.8 5.1 6.6 6.6l2.2-2.2c.3-.3.7-.4 1-.2 1.1.4 2.3.6 3.6.6.6 0 1 .4 1 1V20c0 .6-.4 1-1 1C10.6 21 3 13.4 3 4c0-.6.4-1 1-1h3.5c.6 0 1 .4 1 1 0 1.3.2 2.5.6 3.6.1.3 0 .7-.2 1z"/></svg>
        555 318-0476
      </li>
      <li>
        <svg viewBox="0 0 24 24"><path d="M2 5h20v14H2z M2 5l10 8 10-8" stroke="var(--card)" stroke-width="1.5"/></svg>
        info@falcridgehires.com
      </li>
      <li>
        <svg viewBox="0 0 24 24"><circle cx="12" cy="12" r="10"/></svg>
        www.falcridgehires.com
      </li>
    </ul>
  </section>

</main>
</body>
</html>
```